Single-sided business card for restaurant velmora with new logo made on this site

Business card options with new logo including restaurant name, address, phone number and website. This business card is single-sided only and will be presented at the hostess desk for clients to take. I would like to see options based on a cream card background, a white card background, a yellow card background and a burgundy colored background. It needs to be elegant and traditional.

Target Market(s)

local and international crowd

Industry/Entity Type

restaurant

Contact Information for Business Card

address, website and phone number

Font styles to use
Serif

Colors
EE7325
F08F49
F5BC92
FAE3D3
FDF4ED

Requirements
Must have
• new logo, address, phone number, website
Should not have
• more than three colors

```html
<!DOCTYPE html>
<html lang="es">
<head>
<meta charset="utf-8">
<title>Velmora — Business Card</title>
<link rel="stylesheet" href="https://fonts.googleapis.com/css2?family=Alegreya:wght@400;500&display=swap">
<style>
  :root {
    --backdrop: #2a2a2a;
    --card-yellow: #e6a630;
    --card-yellow-light: #efb233;
    --leaf-shade: #d4962c;
    --burgundy: #4a1a1c;
    --ink-light: #fdf4ed;
  }
  * { box-sizing: border-box; margin: 0; padding: 0; }
  html, body {
    width: 1200px; height: 900px; overflow: hidden;
    background: var(--backdrop);
  }
  .card {
    position: absolute; left: 100px; top: 160px;
    width: 1000px; height: 580px;
    border-radius: 44px;
    background: linear-gradient(110deg, var(--card-yellow) 0%, var(--card-yellow) 55%, var(--card-yellow-light) 100%);
    overflow: hidden;
    font-family: "Alegreya", Georgia, serif;
  }
  .leaf-decoration {
    position: absolute; right: 0; top: 0;
    width: 520px; height: 100%;
    background:
      radial-gradient(ellipse 60% 80% at 55% 60%, rgba(190,130,35,0.45), rgba(190,130,35,0) 70%),
      linear-gradient(160deg, rgba(212,150,44,0.0) 0%, rgba(212,150,44,0.55) 50%, rgba(245,188,60,0.35) 100%);
  }
  .brand {
    position: absolute; left: 250px; top: 150px;
    width: 240px;
    display: flex; flex-direction: column; align-items: center;
    color: var(--burgundy);
  }
  .brand-square {
    width: 150px; height: 150px;
    background: var(--burgundy);
    margin-bottom: 26px;
  }
  .brand-name {
    font-size: 44px; font-weight: 500;
    letter-spacing: 0.16em;
    line-height: 1;
  }
  .brand-since {
    margin-top: 10px;
    font-size: 15px; letter-spacing: 0.12em;
  }
  .divider {
    position: absolute; left: 540px; top: 130px;
    width: 2px; height: 320px;
    background: linear-gradient(180deg, rgba(253,244,237,0) 0%, rgba(253,244,237,0.85) 50%, rgba(253,244,237,0) 100%);
  }
  .contact {
    position: absolute; left: 580px; top: 190px;
    list-style: none;
    color: var(--ink-light);
    font-size: 25px; line-height: 1.3;
  }
  .contact li {
    display: flex; align-items: flex-start; gap: 16px;
    margin-bottom: 18px;
  }
  .contact svg {
    flex: none; width: 22px; height: 22px; margin-top: 5px;
    fill: var(--burgundy);
  }
</style>
</head>
<body>
  <main class="card">
    <div class="leaf-decoration" role="img" aria-label="Faint agave leaf pattern in deeper amber tones"></div>

    <div class="brand">
      <div class="brand-square"></div>
      <div class="brand-name">VELMORA</div>
      <div class="brand-since">DESDE 1999</div>
    </div>

    <div class="divider"></div>

    <ul class="contact">
      <li>
        <svg viewBox="0 0 24 24" aria-hidden="true"><path d="M6.6 10.8a15.1 15.1 0 0 0 6.6 6.6l2.2-2.2a1 1 0 0 1 1-.25 11.4 11.4 0 0 0 3.6.57 1 1 0 0 1 1 1V20a1 1 0 0 1-1 1A17 17 0 0 1 3 4a1 1 0 0 1 1-1h3.5a1 1 0 0 1 1 1c0 1.25.2 2.45.57 3.57a1 1 0 0 1-.25 1z"/></svg>
        <span>958-214-3370</span>
      </li>
      <li>
        <svg viewBox="0 0 24 24" aria-hidden="true"><path d="M12 2a10 10 0 1 0 0 20 10 10 0 0 0 0-20zm6.9 6h-2.9a15.6 15.6 0 0 0-1.4-3.6A8 8 0 0 1 18.9 8zM12 4c.8 1.2 1.5 2.5 1.9 4h-3.8c.4-1.5 1.1-2.8 1.9-4zM4.3 14a8.2 8.2 0 0 1 0-4h3.4a16 16 0 0 0 0 4zm.8 2h2.9c.3 1.3.8 2.5 1.4 3.6A8 8 0 0 1 5.1 16zM8 8H5.1a8 8 0 0 1 4.3-3.6C8.8 5.5 8.3 6.7 8 8zm4 12c-.8-1.2-1.5-2.5-1.9-4h3.8c-.4 1.5-1.1 2.8-1.9 4zm2.3-6H9.7a14.7 14.7 0 0 1 0-4h4.6a14.7 14.7 0 0 1 0 4zm.3 5.6c.6-1.1 1.1-2.3 1.4-3.6h2.9a8 8 0 0 1-4.3 3.6zm1.7-5.6a16 16 0 0 0 0-4h3.4a8.2 8.2 0 0 1 0 4z"/></svg>
        <span>www.velmora.com.mx</span>
      </li>
      <li>
        <svg viewBox="0 0 24 24" aria-hidden="true"><path d="M12 2a7 7 0 0 0-7 7c0 5.2 7 13 7 13s7-7.8 7-13a7 7 0 0 0-7-7zm0 9.5A2.5 2.5 0 1 1 12 6.5a2.5 2.5 0 0 1 0 5z"/></svg>
        <span>Orquídea 517<br>Bahías del Sol<br>Oaxaca, México CP 70452</span>
      </li>
    </ul>
  </main>
</body>
</html>
```